New Business Cards for Tormin Group

We need a new Business Card to compliment our new logo. We are a vibrant design, manufacture and install business providing recreation areas, public parks and Municipal spaces. We want business cards that are classy, modern and clean.

We have recently changed our logo, and are celebrating our 40th anniversary. We want business cards with a new modern design to reflect our status.

Target Market(s)

Customers

Contact Information for Business Card

We need all the details of our 3 offices as per the business card attached. Please disregard the old logo on the business card, the other three files show our new logo.

Requirements
Must have
• All info as per attached business card but with new logo.
Nice to have

```html
<!DOCTYPE html>
<html lang="en">
<head>
<meta charset="utf-8">
<title>Tormin Group – Business Cards</title>
<link rel="stylesheet" href="https://fonts.googleapis.com/css2?family=Work+Sans:wght@400;500;600&display=swap">
<style>
  :root {
    --stage: #1b1b1b;
    --card: #262626;
    --card-edge: #2e2e2e;
    --red: #e5252e;
    --white: #f4f4f4;
  }
  * { box-sizing: border-box; margin: 0; padding: 0; }
  html, body { width: 1200px; height: 900px; overflow: hidden; }
  body {
    background: var(--stage);
    font-family: "Work Sans", sans-serif;
    color: var(--white);
    display: flex;
    flex-direction: column;
    align-items: center;
    justify-content: center;
    gap: 40px;
  }
  .card {
    width: 660px;
    height: 377px;
    background: linear-gradient(135deg, var(--card) 0%, var(--card-edge) 100%);
    position: relative;
    overflow: hidden;
    box-shadow: 0 10px 30px rgba(0,0,0,.5);
  }
  .brand {
    display: flex;
    align-items: center;
    gap: 12px;
    white-space: nowrap;
  }
  .brand__dot {
    width: 42px; height: 42px;
    border-radius: 50%;
    background: var(--red);
    flex: none;
  }
  .brand__name {
    font-weight: 600;
    font-size: 26px;
    letter-spacing: .5px;
    color: var(--white);
    line-height: 1;
  }
  /* Office side */
  .card--offices .brand { position: absolute; left: 56px; top: 46px; }
  .offices {
    position: absolute;
    left: 56px; right: 36px; top: 158px;
    display: grid;
    grid-template-columns: repeat(3, 1fr);
    gap: 20px;
  }
  .office__title {
    color: var(--red);
    font-weight: 500;
    font-size: 17px;
    margin-bottom: 6px;
  }
  .office__address, .office__contacts {
    font-size: 12.5px;
    line-height: 1.45;
    white-space: nowrap;
  }
  .office__contacts { margin-top: 12px; }
  .office__label { color: var(--red); }
  /* Person side */
  .card--person .brand { position: absolute; left: 44px; top: 163px; }
  .card--person .brand__dot { width: 50px; height: 50px; }
  .card--person .brand__name { font-size: 27px; }
  .divider {
    position: absolute;
    left: 348px; top: 112px;
    width: 2px; height: 152px;
    background: var(--red);
  }
  .person {
    position: absolute;
    left: 376px; top: 116px;
    white-space: nowrap;
  }
  .person__name {
    color: var(--red);
    font-weight: 500;
    font-size: 22px;
    letter-spacing: 1px;
  }
  .person__role { font-size: 16px; margin-top: 2px; }
  .person__contacts { list-style: none; margin-top: 18px; }
  .person__contacts li {
    display: flex; align-items: center; gap: 10px;
    font-size: 15px; line-height: 1.7;
  }
  .person__contacts svg { width: 14px; height: 14px; flex: none; }
</style>
</head>
<body>
  <section class="card card--offices">
    <div class="brand">
      <span class="brand__dot"></span>
      <span class="brand__name">TORMIN GROUP</span>
    </div>
    <div class="offices">
      <div class="office">
        <h3 class="office__title">Head Office</h3>
        <p class="office__address">P.O. Box:<br>31480 Abu Dhabi, U.A.E.</p>
        <p class="office__contacts">
          <span class="office__label">P</span> : +971 (0)2 4417250<br>
          <span class="office__label">F</span> : +971 (0)2 4417251<br>
          <span class="office__label">E</span> : sales@tormingroup.com
        </p>
      </div>
      <div class="office">
        <h3 class="office__title">Dubai Office</h3>
        <p class="office__address">P. O. Box:<br>408215 Dubai, U.A.E.</p>
        <p class="office__contacts">
          <span class="office__label">P</span> : +971 (0)4 4382604<br>
          <span class="office__label">F</span> : +971 (0)4 4382605<br>
          <span class="office__label">E</span> : sales@tormingroup.com
        </p>
      </div>
      <div class="office">
        <h3 class="office__title">Qatar Office</h3>
        <p class="office__address">P. O. Box:<br>17342 Doha, Qatar</p>
        <p class="office__contacts">
          <span class="office__label">P</span> : +974 44573018<br>
          <span class="office__label">F</span> : +974 44573019<br>
          <span class="office__label">E</span> : sales@tormingroup.com
        </p>
      </div>
    </div>
  </section>

  <section class="card card--person">
    <div class="brand">
      <span class="brand__dot"></span>
      <span class="brand__name">TORMIN GROUP</span>
    </div>
    <div class="divider"></div>
    <div class="person">
      <h2 class="person__name">KARIM NASSAR</h2>
      <p class="person__role">Managing Partner</p>
      <ul class="person__contacts">
        <li>
          <svg viewBox="0 0 24 24" aria-hidden="true"><path fill="var(--red)" d="M6.6 10.8a15.1 15.1 0 0 0 6.6 6.6l2.2-2.2a1 1 0 0 1 1-.25 11.4 11.4 0 0 0 3.6.57 1 1 0 0 1 1 1V20a1 1 0 0 1-1 1A17 17 0 0 1 3 4a1 1 0 0 1 1-1h3.5a1 1 0 0 1 1 1c0 1.25.2 2.45.57 3.570a1 1 0 0 1-.25 1z"/></svg>
          +971 (0)50 480 7316
        </li>
        <li>
          <svg viewBox="0 0 24 24" aria-hidden="true" fill="none" stroke="var(--red)" stroke-width="2"><rect x="3" y="5" width="18" height="14"/><path d="M3 6l9 7 9-7"/></svg>
          karim@tormingroup.com
        </li>
        <li>
          <svg viewBox="0 0 24 24" aria-hidden="true" fill="none" stroke="var(--red)" stroke-width="2"><circle cx="12" cy="12" r="9"/><path d="M3 12h18M12 3c3 3 3 15 0 18M12 3c-3 3-3 15 0 18"/></svg>
          www.tormingroup.com
        </li>
      </ul>
    </div>
  </section>
</body>
</html>
```